Harvest Gateway Fellowship Ministries needs a fresh new web design

We are an up and coming multicultural church that aims to bring people into a life changing encounter with God. We need a fresh and inviting website in order to increase our internet presence and make us easier to connect with.
Here are some of the basic requirements for the site:
• Clearly displayed address, service times, and contact info
• A staff profile page
• An area for a calendar with upcoming events and their details
• Social media buttons
• Group pages for the different ministries (youth, children’s church, men, etc…)
• An area for donations and eCommerce
• A resources page for assorted media (podcasts, sermons, videos, etc.…)
• An area for prayer requests.

```html
<!DOCTYPE html>
<html lang="en">
<head>
<meta charset="utf-8">
<title>Harvest Gateway Fellowship Ministries – About</title>
<link href="https://fonts.googleapis.com/css2?family=Lato:wght@300;400;700&display=swap" rel="stylesheet">
<style>
:root{
  --navy:#1d1192;
  --navy-text:#c9c4ee;
  --gold:#e6c20a;
  --gold-text:#d8b40c;
  --ink:#4a4a4a;
  --muted:#7a7a7a;
  --page:#f2f2f2;
  --line:#dcdcdc;
  --icon:#b8b8b8;
}
*{box-sizing:border-box;margin:0;padding:0}
html,body{width:1037px;height:1200px;overflow:hidden}
body{font-family:'Lato',sans-serif;color:var(--ink);background:var(--page);position:relative}
.abs{position:absolute}

.topbar{left:0;top:0;width:1037px;height:34px;background:var(--navy);color:#fff;font-size:12.5px}
.topbar .tagline{left:87px;top:10px}
.topbar .schedule-label{left:636px;top:11px;font-size:12px}
.topbar .schedule{left:797px;top:5px;padding-left:8px;border-left:2px solid #fff;font-size:10.5px;line-height:12px}

.header{left:0;top:34px;width:1037px;height:100px;background:#fff}
.brand{left:88px;top:22px;display:flex;align-items:center;gap:8px}
.brand-dot{width:40px;height:40px;border-radius:50%;background:var(--navy)}
.brand-name{font-size:16px;font-weight:700;color:var(--navy);line-height:18px;width:165px}
.info{top:22px;text-align:right;font-size:12.5px;line-height:13px;color:var(--muted)}
.info h3{font-size:14px;font-weight:700;color:#555;margin-bottom:5px}
.info a{font-size:10.5px;color:var(--gold-text);text-decoration:none}
.info.donate{left:340px;width:154px}
.info.prayer{left:520px;width:218px}
.info.address{left:762px;width:130px}
.vrule{top:24px;width:1px;height:56px;background:var(--line)}
.social-dot{width:23px;height:23px;border-radius:50%;background:var(--icon)}

.nav{left:0;top:134px;width:1037px;height:35px;background:var(--gold);display:flex;align-items:center;padding-left:78px;font-size:12.5px;color:#3a3210}
.nav span{padding:0 22px;border-right:1px solid #c9a806;line-height:14px}
.nav span:last-child{border:none}

.banner{left:0;top:169px;width:1037px;height:87px;background:linear-gradient(90deg,#2a1a05,#6b4a0f 35%,#3d2a08 60%,#7a5812 85%,#2a1a05)}
.crumb{left:87px;top:193px;color:#fff;font-size:12px}
.page-title{left:87px;top:207px;color:#fff;font-size:23px;font-weight:700}

.intro{left:95px;top:303px;width:548px;font-size:12.5px;line-height:19px;color:#555}
.intro p+p{margin-top:19px}
.sec-title{font-size:20px;font-weight:300;color:var(--gold-text);border-bottom:1px solid #d9c46a;padding-bottom:4px}
.pastors-title{left:95px;top:480px;width:543px}

.pastor{top:535px;width:172px;text-align:center}
.pastor .photo{width:172px;height:139px;border:1px solid #e2e2e2;background:radial-gradient(circle,#fff,#e9e9e9)}
.pastor .photo.real{background:radial-gradient(circle at 50% 45%,#6a4a35,#b0682a 70%,#8a4f1d)}
.pastor h4{font-size:16px;font-weight:400;color:#333;margin-top:14px}
.pastor .role{font-size:11.5px;font-style:italic;color:#aaa;margin-top:2px}
.pastor p{font-size:11.5px;line-height:16.5px;color:#555;margin-top:4px}
.pastor .icons{display:flex;justify-content:center;gap:6px;margin-top:14px}
.pastor .icons i{width:22px;height:22px;border-radius:50%;background:#c4c4c4}

.btn{left:263px;top:844px;width:208px;height:43px;border:2px solid var(--gold);color:var(--gold-text);font-size:13.5px;display:flex;align-items:center;justify-content:center}

.events-title{left:682px;top:303px;width:269px}
.event{left:682px;width:269px;border-bottom:1px solid #e2e2e2;height:102px}
.event .date{font-size:25px;font-weight:300;color:var(--gold-text);line-height:26px}
.event .date b{font-weight:700}
.event h4{font-size:16.5px;font-weight:700;color:#444;margin-top:1px}
.event p{font-size:11.5px;line-height:17px;color:#777;margin-top:2px}
.event.last{border:none}

.footer{left:0;top:938px;width:1037px;height:262px;background:var(--navy);color:var(--navy-text)}
.fcol{top:36px;font-size:12px;line-height:16px}
.fcol h5{font-size:16.5px;font-weight:300;color:#fff;margin-bottom:10px}
.fcol ul{list-style:none;line-height:21px}
.contact-line{display:flex;align-items:center;gap:8px;margin-top:6px;font-size:12.5px}
.email-field{width:197px;height:29px;background:#fff;border-radius:3px;margin-top:8px;color:#aaa;padding:7px 10px}
.subscribe{width:81px;height:29px;background:var(--gold);border-radius:3px;color:#222;margin-top:9px;display:flex;align-items:center;justify-content:center}
.fsocial{display:flex;gap:8px;margin-top:6px}
.fsocial i{width:27px;height:27px;border-radius:50%;background:#a7a2dc}
.frule{left:86px;top:195px;width:865px;height:1px;background:#3b30a6}
.copyright{left:0;top:210px;width:1037px;text-align:center;font-size:11px;color:#a9a3dc}
</style>
</head>
<body>

<div class="abs topbar">
  <div class="abs tagline">A house of prayer for all nations, where the love, the presence and the power of God are real.</div>
  <div class="abs schedule-label">SUNDAY SERVICE SCHEDULE</div>
  <div class="abs schedule">09:00 A.M. | Sunday School<br>10:30 A.M. | Convergent Service</div>
</div>

<header class="abs header">
  <div class="abs brand"><div class="brand-dot"></div><div class="brand-name">Harvest Gateway Fellowship Ministries</div></div>
  <div class="abs info donate"><h3>Donate</h3>Lorem Ipsum is simply<br>dummy text of the printing<br><a>Donate Now »</a></div>
  <div class="abs vrule" style="left:512px"></div>
  <div class="abs info prayer"><h3>Request Prayer</h3>Lorem Ipsum is simply dummy text<br>of the printing and typesetting industry.<br><a>Request Now »</a></div>
  <div class="abs vrule" style="left:756px"></div>
  <div class="abs info address"><h3>Address</h3>Harvest Gateway<br>City, Location<br><a>Contact »</a></div>
  <div class="abs vrule" style="left:909px"></div>
  <div class="abs social-dot" style="left:927px;top:26px" aria-label="Social link"></div>
  <div class="abs social-dot" style="left:927px;top:53px" aria-label="Social link"></div>
</header>

<nav class="abs nav">
  <span>Home</span><span>About</span><span>Staff Profile</span><span>News and Events</span><span>Worship &amp; Services</span><span>Groups</span><span>Shop</span><span>Resources</span><span>Contact</span>
</nav>

<div class="abs banner" role="img" aria-label="Golden wheat field banner"></div>
<div class="abs crumb">Home &gt; <b>About</b></div>
<h1 class="abs page-title">About</h1>

<section class="abs intro">
  <p>Lorem Ipsum is simply dummy text of the printing and typesetting industry. Lorem Ipsum has been the industry's standard dummy text ever since the 1500s, when an unknown printer took a galley of type and scrambled it to make a type specimen book.</p>
  <p>It has survived not only five centuries, but also the leap into electronic typesetting, remaining essentially unchanged. It was popularised in the 1960s with the release of Letraset sheets containing Lorem Ipsum passages, and more recently with desktop publishing software like Aldus PageMaker including versions of Lorem Ipsum.</p>
</section>

<h2 class="abs sec-title pastors-title">PASTORS</h2>

<div class="abs pastor" style="left:95px">
  <div class="photo real" role="img" aria-label="Portrait photo of pastor Samuel Okoro"></div>
  <h4>SAMUEL OKORO</h4><div class="role">Designation</div>
  <p>Lorem Ipsum is simply dummy text of the printing and typesetting industry industry's standard.</p>
  <div class="icons"><i></i><i></i></div>
</div>
<div class="abs pastor" style="left:281px">
  <div class="photo" role="img" aria-label="Pastor photo placeholder"></div>
  <h4>JOHN DOE</h4><div class="role">Designation</div>
  <p>Lorem Ipsum is simply dummy text of the printing and typesetting industry industry's standard.</p>
  <div class="icons"><i></i><i></i></div>
</div>
<div class="abs pastor" style="left:467px">
  <div class="photo" role="img" aria-label="Pastor photo placeholder"></div>
  <h4>JOHN DOE</h4><div class="role">Designation</div>
  <p>Lorem Ipsum is simply dummy text of the printing and typesetting industry industry's standard.</p>
  <div class="icons"><i></i><i></i></div>
</div>

<div class="abs btn">VIEW STAFF PROFILE</div>

<h2 class="abs sec-title events-title">UPCOMING EVENTS</h2>
<div class="abs event" style="top:355px"><div class="date"><b>29</b> JUL</div><h4>Vacation Bible School</h4><p>Lorem Ipsum is simply dummy text of the printing and typesetting industry.</p></div>
<div class="abs event" style="top:457px"><div class="date"><b>20</b> JUL</div><h4>Vacation Bible School</h4><p>Lorem Ipsum is simply dummy text of the printing and typesetting industry.</p></div>
<div class="abs event" style="top:559px"><div class="date"><b>28</b> JUN</div><h4>Vacation Bible School</h4><p>Lorem Ipsum is simply dummy text of the printing and typesetting industry.</p></div>
<div class="abs event last" style="top:661px"><div class="date"><b>19</b> JUN</div><h4>Family and Friends Day</h4><p>Sunday June 29th is our family and friends day with special guest pastor Daniel Mensah. Come with faith..</p></div>

<footer class="abs footer">
  <div class="abs fcol" style="left:86px">
    <h5>CONTACT US</h5>
    Harvest Gateway<br>Location, city<br>State Name, Country
    <div class="contact-line" style="margin-top:10px">
      <svg width="13" height="13" viewBox="0 0 24 24"><path fill="#c9c4ee" d="M6.6 10.8a15 15 0 006.6 6.6l2.2-2.2a1 1 0 011-.25 11.4 11.4 0 003.6.6 1 1 0 011 1V20a1 1 0 01-1 1A17 17 0 013 4a1 1 0 011-1h3.5a1 1 0 011 1 11.4 11.4 0 00.6 3.6 1 1 0 01-.25 1z"/></svg>
      +1 888-555-0142</div>
    <div class="contact-line">
      <svg width="14" height="11" viewBox="0 0 14 11"><rect width="14" height="11" fill="#c9c4ee"/><path d="M0 0l7 6 7-6" stroke="#1d1192" fill="none"/></svg>
      hgfministries@example.com</div>
  </div>
  <div class="abs fcol" style="left:278px">
    <h5>COMMUNITIES WE SERVE</h5>
    <div style="display:flex;gap:12px">
      <ul><li>• Lorem Ipsum</li><li>• Dummy Links</li><li>• More dummy</li><li>• Sample Text</li><li>• More samples</li></ul>
      <ul><li>• type text dummy</li><li>• Lorem Ipsum</li></ul>
    </div>
  </div>
  <div class="abs fcol" style="left:518px">
    <h5>NEWSLETTER</h5>
    Enter your email below to get notified
    <div class="email-field">Your Email</div>
    <div class="subscribe">Subscribe</div>
  </div>
  <div class="abs fcol" style="left:758px;width:200px">
    <h5>CONNECT WITH US</h5>
    Stay connected for the latest updates at Harvest Gateway Fellowship
    <div class="fsocial"><i></i><i></i></div>
  </div>
  <div class="abs frule"></div>
  <div class="abs copyright">Copyright © 2014. All rights reserved. Harvest Gateway.</div>
</footer>

</body>
</html>
```